Modern business card design for professional copywriter

I'd like a business card design that I can use to have my cards printed out by quillprint.com as a squared corners business card (see artwork and design guidelines here: https://help.quillprint.com/hc/en-gb/sections/200570950-QUILL-Product-Templates)

The design should be clean and modern and reflect the colours, tone and branding on my website: https://tessavorrin.com.au

Target Market(s)

Professionals, B2B small business owners

Industry/Entity Type

Business

Contact Information for Business Card

Tessa Vorrin
m: 0468 905 327
e: tessa@tessavorrin.com.au
w: tessavorrin.com.au

Font styles to use
Sans Serif

Requirements
Must have
• Tagline: "Smart copywriting for clever business people"
• Brand colours: fd8000, 009984, 666666 and black
Nice to have

```html
<!DOCTYPE html>
<html lang="en">
<head>
<meta charset="utf-8">
<title>Tessa Vorrin – Business Card</title>
<link rel="stylesheet" href="https://fonts.googleapis.com/css2?family=Jost:wght@400;500&family=Oswald:wght@500&display=swap">
<style>
  :root {
    --orange: #fd8000;
    --teal: #009984;
    --grey: #666666;
    --black: #000000;
    --paper: #ffffff;
    --backdrop: #eeece7;
  }
  * { box-sizing: border-box; margin: 0; padding: 0; }
  html, body { width: 1200px; height: 929px; overflow: hidden; }
  body {
    background: var(--backdrop);
    font-family: "Jost", sans-serif;
    display: flex;
    align-items: center;
    justify-content: center;
    gap: 40px;
  }
  .card {
    position: relative;
    width: 520px;
    height: 336px;
    background: var(--paper);
    box-shadow: 0 2px 6px rgba(0,0,0,0.12);
    overflow: hidden;
  }
  .card__band {
    position: absolute;
    left: 0; right: 0; bottom: 0;
    height: 16px;
  }
  .card--front .card__band { background: var(--orange); }
  .card--back .card__band { background: var(--teal); }

  /* Front */
  .brand {
    position: absolute;
    inset: 0 0 16px 0;
    display: flex;
    align-items: center;
    justify-content: center;
    gap: 12px;
  }
  .brand__mark {
    width: 18px; height: 18px;
    background: var(--orange);
  }
  .brand__name {
    font-family: "Jost", sans-serif;
    font-weight: 500;
    font-size: 44px;
    color: var(--teal);
    letter-spacing: -0.5px;
  }

  /* Back */
  .identity {
    position: absolute;
    left: 60px;
    top: 104px;
    display: flex;
    align-items: center;
  }
  .identity__who { text-align: right; padding-right: 22px; }
  .identity__name {
    font-family: "Oswald", sans-serif;
    font-weight: 500;
    font-size: 34px;
    line-height: 1;
    color: var(--teal);
    letter-spacing: 0.5px;
  }
  .identity__role {
    font-size: 17px;
    color: var(--grey);
    margin-top: 2px;
  }
  .identity__divider {
    width: 2px;
    height: 62px;
    background: var(--orange);
  }
  .contact {
    list-style: none;
    padding-left: 18px;
    font-size: 14px;
    color: var(--grey);
    line-height: 1.45;
  }
  .contact li { display: flex; align-items: center; gap: 8px; }
  .contact svg { width: 11px; height: 11px; flex: none; }
  .tagline {
    position: absolute;
    left: 0; right: 0;
    bottom: 58px;
    text-align: center;
    font-size: 14px;
    letter-spacing: 0.6px;
    color: var(--grey);
  }
</style>
</head>
<body>
  <section class="card card--front" aria-label="Card front">
    <div class="brand">
      <span class="brand__mark"></span>
      <span class="brand__name">Tessa Vorrin</span>
    </div>
    <div class="card__band"></div>
  </section>

  <section class="card card--back" aria-label="Card back">
    <div class="identity">
      <div class="identity__who">
        <div class="identity__name">TESSA VORRIN</div>
        <div class="identity__role">Copywriter</div>
      </div>
      <div class="identity__divider"></div>
      <ul class="contact">
        <li>
          <svg viewBox="0 0 12 12" aria-hidden="true"><rect x="3" y="0.8" width="6" height="10.4" rx="1" fill="none" stroke="#009984" stroke-width="1.2"/></svg>
          0468 905 327
        </li>
        <li>
          <svg viewBox="0 0 12 12" aria-hidden="true"><rect x="1" y="2.5" width="10" height="7" fill="#009984"/><path d="M1 2.5 L6 6.5 L11 2.5" fill="none" stroke="#fff" stroke-width="1"/></svg>
          tessa@tessavorrin.com.au
        </li>
        <li>
          <svg viewBox="0 0 12 12" aria-hidden="true"><circle cx="5" cy="5" r="3.4" fill="none" stroke="#009984" stroke-width="1.5"/><path d="M7.5 7.5 L11 11" stroke="#009984" stroke-width="1.6"/></svg>
          tessavorrin.com.au
        </li>
      </ul>
    </div>
    <p class="tagline">Smart copywriting for clever business people</p>
    <div class="card__band"></div>
  </section>
</body>
</html>
```